Quillbrook IT company focused on 3 areas of IT

Looking for something similar to attached cards. Logo for quillbrook also attached.. Looking for something clean as far as colors (surprise me).. Quill stands for 3 primary areas, web design, consulting and network infrastructure design. Please email me if you have any questions. Looking forward to seeing how creative and professional this card will look. Thank you,

Target Market(s)

Small business/consumers looking for It services

Industry/Entity Type

It Service

Contact Information for Business Card

Dorin Vasek
Principal Consultant

202-555-0173

www.quillbrook-example.com
dvasek@quillbrook-example.com

27416 Copper Lantern Way,
Germantown, MD 20999

Colors

Designer to choose colors to be used in the design.

Requirements
Must have
• attached Logo design. Feel free to play with the colors.. If you have a better idea for a card, please fee free to send me. Looking for something clean/modern. Should have tech feel, not cheesy.
Nice to have
• Surprise me :-)..

```html
<!DOCTYPE html>
<html lang="en">
<head>
<meta charset="utf-8">
<title>Quillbrook Business Card</title>
<link href="https://fonts.googleapis.com/css2?family=Oswald:wght@600&family=Work+Sans:wght@400;500&display=swap" rel="stylesheet">
<style>
  :root {
    --page-bg: #e4e6ea;
    --card-white: #ffffff;
    --brand-blue: #1f3a7a;
    --brand-blue-deep: #182f66;
    --text-grey: #4a4d54;
    --logo-grey: #c9ccd3;
  }
  html, body {
    margin: 0;
    padding: 0;
    width: 1200px;
    height: 900px;
    overflow: hidden;
    background: var(--page-bg);
  }
  .canvas {
    position: relative;
    width: 1200px;
    height: 900px;
  }
  .card {
    position: absolute;
    left: 320px;
    width: 560px;
    height: 320px;
    border-radius: 18px;
    box-shadow: 0 8px 24px rgba(20, 30, 60, 0.18);
    overflow: hidden;
  }
  .card--front {
    top: 110px;
    background: var(--card-white);
    font-family: "Work Sans", Arial, sans-serif;
  }
  .card--back {
    top: 470px;
    background: linear-gradient(160deg, var(--brand-blue) 0%, var(--brand-blue-deep) 100%);
    display: flex;
    align-items: center;
    justify-content: center;
  }
  .identity {
    position: absolute;
    left: 44px;
    top: 96px;
    width: 210px;
  }
  .identity__name {
    margin: 0;
    font-family: "Oswald", "Arial Narrow", sans-serif;
    font-weight: 600;
    font-size: 34px;
    line-height: 1;
    letter-spacing: 1px;
    text-transform: uppercase;
    color: var(--brand-blue);
  }
  .identity__title {
    margin: 6px 0 0;
    font-size: 14px;
    color: var(--text-grey);
  }
  .divider {
    position: absolute;
    left: 270px;
    top: 100px;
    width: 2px;
    height: 82px;
    background: var(--brand-blue);
  }
  .contact-list {
    position: absolute;
    left: 292px;
    top: 104px;
    margin: 0;
    padding: 0;
    list-style: none;
    font-size: 13px;
    color: var(--text-grey);
  }
  .contact-list li {
    display: flex;
    align-items: center;
    gap: 8px;
    margin-bottom: 9px;
  }
  .contact-list svg {
    width: 12px;
    height: 12px;
    flex: none;
  }
  .contact-list .accent { color: var(--brand-blue); }
  .address {
    position: absolute;
    left: 44px;
    bottom: 40px;
    margin: 0;
    font-size: 13px;
    color: var(--text-grey);
  }
  .logo-name {
    font-family: "Work Sans", Arial, sans-serif;
    font-weight: 500;
    font-size: 60px;
    letter-spacing: 2px;
    text-transform: uppercase;
    color: var(--logo-grey);
  }
</style>
</head>
<body>
<div class="canvas">
  <section class="card card--front">
    <div class="identity">
      <h1 class="identity__name">Dorin Vasek</h1>
      <p class="identity__title">Principal Consultant</p>
    </div>
    <div class="divider"></div>
    <ul class="contact-list">
      <li>
        <svg viewBox="0 0 12 12" aria-hidden="true"><path d="M2.5 1h2l1 3-1.4 1a6 6 0 0 0 2.9 2.9l1-1.4 3 1v2c0 .6-.4 1-1 1A9.5 9.5 0 0 1 1.5 2c0-.6.4-1 1-1z" fill="#1f3a7a"/></svg>
        <span>202-555-0173</span>
      </li>
      <li>
        <svg viewBox="0 0 12 12" aria-hidden="true"><rect x="1" y="2.5" width="10" height="7" rx="1" fill="none" stroke="#1f3a7a" stroke-width="1.2"/><path d="M1.5 3l4.5 3.5L10.5 3" fill="none" stroke="#1f3a7a" stroke-width="1.2"/></svg>
        <span>dvasek@quillbrook-example.com</span>
      </li>
      <li>
        <svg viewBox="0 0 12 12" aria-hidden="true"><circle cx="6" cy="6" r="5" fill="none" stroke="#1f3a7a" stroke-width="1.1"/><ellipse cx="6" cy="6" rx="2.2" ry="5" fill="none" stroke="#1f3a7a" stroke-width="1"/><path d="M1 6h10" stroke="#1f3a7a" stroke-width="1"/></svg>
        <span>www.<span class="accent">quillbrook-example</span>.com</span>
      </li>
    </ul>
    <p class="address">27416 Copper Lantern Way, Germantown, MD 20999</p>
  </section>
  <section class="card card--back">
    <span class="logo-name">Quillbrook</span>
  </section>
</div>
</body>
</html>
```